New Business Card Design Project LORVANTI-Italy

we are LORVANTI-Italy
our company in the market for 3 years we are luxury cosmetic company and its about time for a facelift :)
i will like to have elegant luxurious and unique business card
that will give the person that get it a unique, luxurious and elegant impression
I'm VERY OPEN FOR NEW IDEAS , even duo i add a few files of things that i see on line and i like them

i add my logo as well
my website is LORVANTI.COM
(if you would like to see the main style that we have)

Target Market(s)

adult that have money :)

Industry/Entity Type

Business

Contact Information for Business Card

Name - Dario Lorvanti
Position - CEO and CO Founder
address - 4817 E Halvern
telephone - 555-384-1926
email - dario@lorvanti.com
fax - 555-384-1926
website - LORVANTI.COM

Colors
000000
959595
fbee3e
ffffff

Requirements
Must have
• big logo in GOLD color
• elegant look
• impressive
Nice to have
• not must but maybe classy pattern background
• not must but maybe emblem
• maybe clear plastic business card
Should not have
• colors
• images

```html
<!DOCTYPE html>
<html lang="en">
<head>
<meta charset="utf-8">
<title>LORVANTI Italy – Business Card</title>
<link rel="stylesheet" href="https://fonts.googleapis.com/css2?family=Cormorant+Garamond:wght@500;600&family=Open+Sans:wght@400&display=swap">
<style>
  :root {
    --bg: #e6e2db;
    --card: #232323;
    --card-edge: #1b1b1b;
    --gold: #d6a92e;
    --gold-soft: #c8992a;
    --text-light: #e4e4e4;
    --emboss: #171717;
    --emboss-line: #3a3a3a;
  }
  * { box-sizing: border-box; margin: 0; padding: 0; }
  html, body { width: 1200px; height: 900px; overflow: hidden; }
  body {
    background: var(--bg);
    display: flex;
    flex-direction: column;
    align-items: center;
    justify-content: center;
    gap: 56px;
    font-family: "Open Sans", Arial, sans-serif;
  }
  .card {
    position: relative;
    width: 560px;
    height: 320px;
    background: var(--card);
    border: 1px solid var(--card-edge);
    box-shadow: 0 10px 24px rgba(0,0,0,0.25);
  }
  .wordmark {
    font-family: "Cormorant Garamond", Georgia, serif;
    font-weight: 600;
    color: var(--gold);
    letter-spacing: 2px;
    line-height: 1;
  }
  .rule { height: 2px; background: var(--gold); }
  .origin {
    font-family: "Cormorant Garamond", Georgia, serif;
    font-weight: 600;
    color: var(--gold);
    letter-spacing: 2px;
  }

  /* Front */
  .card-front { display: flex; flex-direction: column; align-items: center; padding-top: 42px; }
  .card-front .mark { width: 84px; height: 84px; }
  .card-front .wordmark { font-size: 56px; margin-top: 18px; }
  .card-front .rule { width: 270px; margin-top: 4px; }
  .card-front .origin { font-size: 18px; margin-top: 6px; }
  .card-front .site { font-size: 13px; color: var(--gold); margin-top: 16px; letter-spacing: 0.5px; }

  /* Back */
  .card-back .brand { position: absolute; left: 44px; top: 40px; width: 290px; text-align: center; }
  .card-back .wordmark { font-size: 54px; }
  .card-back .rule { width: 290px; margin-top: 4px; }
  .card-back .origin { font-size: 18px; margin-top: 6px; }
  .card-back .emblem { position: absolute; right: 34px; top: 64px; width: 172px; height: 172px; }
  .person { position: absolute; left: 44px; top: 182px; }
  .person-name {
    font-family: "Cormorant Garamond", Georgia, serif;
    font-weight: 600; font-size: 21px; color: var(--gold); letter-spacing: 1px;
  }
  .person-role { font-size: 12px; color: var(--text-light); margin-top: 2px; }
  .contacts { list-style: none; margin-top: 12px; }
  .contacts li {
    display: flex; align-items: center; gap: 8px;
    font-size: 12.5px; color: var(--text-light); height: 18px;
  }
  .contacts svg { width: 12px; height: 12px; fill: var(--gold); flex: none; }
</style>
</head>
<body>

  <section class="card card-front">
    <svg class="mark" viewBox="0 0 84 84" aria-hidden="true">
      <circle cx="42" cy="42" r="39" fill="none" stroke="var(--gold)" stroke-width="3"/>
    </svg>
    <div class="wordmark">LORVANTI</div>
    <div class="rule"></div>
    <div class="origin">ITALY</div>
    <div class="site">www.lorvanti.com</div>
  </section>

  <section class="card card-back">
    <div class="brand">
      <div class="wordmark">LORVANTI</div>
      <div class="rule"></div>
      <div class="origin">ITALY</div>
    </div>

    <svg class="emblem" viewBox="0 0 172 172" aria-hidden="true">
      <circle cx="86" cy="86" r="82" fill="var(--emboss)" stroke="var(--emboss-line)" stroke-width="2"/>
    </svg>

    <div class="person">
      <div class="person-name">DARIO LORVANTI</div>
      <div class="person-role">CEO and CO Founder</div>
      <ul class="contacts">
        <li>
          <svg viewBox="0 0 24 24"><path d="M6.6 10.8a15 15 0 0 0 6.6 6.6l2.2-2.2c.3-.3.7-.4 1-.2 1.1.4 2.3.6 3.6.6.6 0 1 .4 1 1V20c0 .6-.4 1-1 1A17 17 0 0 1 3 4c0-.6.4-1 1-1h3.5c.6 0 1 .4 1 1 0 1.3.2 2.5.6 3.6.1.3 0 .7-.2 1z"/></svg>
          555-384-1926
        </li>
        <li>
          <svg viewBox="0 0 24 24"><path d="M6 2h9l3 3v4H6zM3 10h18v9h-3v3H6v-3H3zm5 6v4h8v-4z"/></svg>
          555-384-1926
        </li>
        <li>
          <svg viewBox="0 0 24 24"><path d="M2 5h20v14H2zm2 2v.5l8 5.5 8-5.5V7z"/></svg>
          dario@lorvanti.com
        </li>
        <li>
          <svg viewBox="0 0 24 24"><path d="M12 2a7 7 0 0 0-7 7c0 5 7 13 7 13s7-8 7-13a7 7 0 0 0-7-7zm0 9.5a2.5 2.5 0 1 1 0-5 2.5 2.5 0 0 1 0 5z"/></svg>
          4817 E Halvern
        </li>
      </ul>
    </div>
  </section>

</body>
</html>
```